Business Card Design For Marketing Agnecy LVP

Need business card design for marketing agency.

Doug Fenwick
President, CEO
1-555-302-4196
doug@boldpromoperksgroup.example
www.BoldPromoPerksGroup.example

Back Side:
Boost Sales Using Rewards, Incentives & Giveaways
Get A Free Sample Package

Target Market(s)

B2B

Industry/Entity Type

Marketing

Contact Information for Business Card

Doug Fenwick
President, CEO
1-555-302-4196

Back Side:
Get A Free Sample Package

Please note that my current url is OLD DESIGN. I am working on new design and want the business card to match color themes at least on new site. Here is the demo link for new site so you can see the colors I use, etc.

http://layoutcratehub.example/kq/doug/lvp_final/index.html

Requirements
Must have
• Please note that my current url is OLD DESIGN. I am working on new design and want the business card to match color themes at least on new site. Here is the demo link for new site so you can see the colors I use, etc.

Nice to have

Should not have

```html
<!DOCTYPE html>
<html lang="en">
<head>
<meta charset="utf-8">
<title>LVP Business Card</title>
<link rel="stylesheet" href="https://fonts.googleapis.com/css2?family=Roboto:wght@400;500;700&family=Roboto+Condensed:wght@400&family=Exo+2:wght@600&display=swap">
<style>
  :root {
    --page: #e4e4e4;
    --brand-blue: #2b5a97;
    --ink-dark: #3a3a3c;
    --ink-text: #333333;
    --card-white: #f4f4f4;
    --banner-white: #f1f1f1;
  }
  * { margin: 0; padding: 0; box-sizing: border-box; }
  html, body { width: 1200px; height: 576px; overflow: hidden; }
  body { background: var(--page); font-family: "Roboto", sans-serif; position: relative; }

  .card {
    position: absolute;
    top: 138px;
    width: 483px;
    height: 294px;
    border-radius: 10px;
    overflow: hidden;
  }
  .card--front { left: 82px; background: var(--brand-blue); color: #fff; }
  .card--back { left: 602px; background: var(--card-white); }

  /* Front */
  .front-logo {
    position: absolute; top: 36px; left: 0; right: 0;
    display: flex; justify-content: center; align-items: center; gap: 12px;
  }
  .front-logo__mark { width: 20px; height: 20px; border-radius: 50%; background: #fff; }
  .front-logo__name {
    font-family: "Roboto", sans-serif; font-weight: 700; font-size: 84px;
    letter-spacing: -2px; color: #fff; line-height: 1;
  }
  .offer-banner { position: absolute; left: 62px; top: 194px; width: 359px; height: 52px; }
  .offer-banner svg { position: absolute; inset: 0; }
  .offer-banner__text {
    position: relative; text-align: center; padding-top: 7px; line-height: 1.45;
  }
  .offer-banner__lead { font-size: 12.5px; color: var(--ink-text); }
  .offer-banner__cta { font-size: 12.5px; font-weight: 700; color: var(--brand-blue); }
  .front-url {
    position: absolute; top: 257px; left: 0; right: 0;
    text-align: center; font-size: 12.5px; color: #fff;
  }

  /* Back */
  .back-logo {
    position: absolute; top: 44px; left: 36px;
    display: flex; align-items: center; gap: 10px;
  }
  .back-logo__mark { width: 14px; height: 14px; border-radius: 50%; background: var(--brand-blue); }
  .back-logo__name {
    font-family: "Roboto", sans-serif; font-weight: 700; font-size: 52px;
    letter-spacing: -1px; color: var(--brand-blue); line-height: 1;
  }
  .contact-list {
    position: absolute; top: 141px; left: 36px; list-style: none;
    font-family: "Roboto Condensed", sans-serif; font-size: 12px; color: var(--ink-text);
  }
  .contact-list li { display: flex; align-items: center; gap: 8px; height: 18px; }
  .contact-list svg { width: 11px; height: 11px; fill: var(--brand-blue); }
  .back-wave { position: absolute; left: 0; top: 0; }
  .holder {
    position: absolute; right: 24px; top: 226px; text-align: right; color: #fff;
  }
  .holder__name { font-family: "Exo 2", sans-serif; font-weight: 600; font-size: 18px; }
  .holder__title { font-family: "Roboto Condensed", sans-serif; font-size: 12px; margin-top: 2px; }
</style>
</head>
<body>

<section class="card card--front">
  <div class="front-logo">
    <span class="front-logo__mark"></span>
    <span class="front-logo__name">LVP</span>
  </div>
  <div class="offer-banner">
    <svg width="359" height="52" viewBox="0 0 359 52">
      <path d="M0,0 H359 L352,42 L180,52 L7,42 Z" fill="var(--banner-white)"/>
    </svg>
    <div class="offer-banner__text">
      <p class="offer-banner__lead">Boost Sales Using Rewards, Incentives &amp; Giveaways</p>
      <p class="offer-banner__cta">GET A FREE SAMPLE PACKAGE</p>
    </div>
  </div>
  <p class="front-url">www.BoldPromoPerksGroup.example</p>
</section>

<section class="card card--back">
  <div class="back-logo">
    <span class="back-logo__mark"></span>
    <span class="back-logo__name">LVP</span>
  </div>
  <ul class="contact-list">
    <li>
      <svg viewBox="0 0 12 12"><path d="M1,3 Q6,0 11,3 L10,5 L8,4 L8,3 L4,3 L4,4 L2,5 Z M3,6 H9 L10,11 H2 Z"/></svg>
      1-555-302-4196
    </li>
    <li>
      <svg viewBox="0 0 12 12"><path d="M0,2 H12 V10 H0 Z M1,3 L6,7 L11,3 Z" fill-rule="evenodd"/></svg>
      doug@boldpromoperksgroup.example
    </li>
    <li>
      <svg viewBox="0 0 12 12"><circle cx="6" cy="6" r="5.5"/><path d="M6,0.5 V11.5 M0.5,6 H11.5 M6,0.5 Q2,6 6,11.5 M6,0.5 Q10,6 6,11.5" stroke="#fff" stroke-width="0.8" fill="none"/></svg>
      www.BoldPromoPerksGroup.example
    </li>
  </ul>
  <svg class="back-wave" width="483" height="294" viewBox="0 0 483 294">
    <path d="M0,226 C100,272 220,270 330,220 C385,196 435,186 483,188 L483,200 C432,200 385,212 332,234 C220,280 100,276 0,248 Z" fill="var(--ink-dark)"/>
    <path d="M0,262 C120,292 240,272 342,236 C402,214 442,206 483,204 L483,294 L0,294 Z" fill="var(--brand-blue)"/>
  </svg>
  <div class="holder">
    <p class="holder__name">Doug Fenwick</p>
    <p class="holder__title">President, CEO</p>
  </div>
</section>

</body>
</html>
```